Zielgruppe
Wir sind ein Business Center und vermieten Büro- und Konferenzräume. Wir richten uns an Unternehmen unterschiedlichster Branchen: Freelancer ohne eigenes Büro oder auch große Unternehmen, welche keine eigene freien Vakanzen haben, z. B. für Vorstellungsgespräche.
Aufgabenstellung
Flyer Din Lang, quer, gebunden an der kurzen Seite. 8 Seiten, inkl. Vorder- und Rückseite. Bitte kein Wickelfalz oder ähnliches, sondern eine Broschüre, gebunden mit Klammerheftung!!!
Frisches helles Design, ohne Schnörkel. Bilder mit etwas Text, dazu eine Seite über uns. Rückseite Kontaktdaten. Je eine Doppelseite für Konferenzraumvermietung und eine Doppelseite für Büroraum auf Zeit, eine Doppelseite für unsere weitere Leistungen, Telefonservice (Anrufannahme im namen unserer Kunden).
Unsere Räume sind sehr repräsentativ und modern eingerichtet mit hellen Designermöbeln. Das soll auch in der Broschüre klar werden.

```html
<!DOCTYPE html>
<html lang="de">
<head>
<meta charset="utf-8">
<title>Kelvora Broschüre</title>
<link rel="stylesheet" href="https://fonts.googleapis.com/css2?family=Barlow:wght@300;400;600;700&family=Barlow+Semi+Condensed:wght@400;600;700&display=swap">
<style>
:root{
  --bg:#bcbcbc;
  --paper:#ffffff;
  --green:#c4ca52;
  --sand:#dcd5cf;
  --sand-light:#e2deda;
  --ink:#3a3a3a;
  --ink-soft:#555;
  --title-grey:#a8a79a;
  --photo-warm:#c9b9a4;
  --photo-cool:#cfd3d6;
  --photo-dark:#4a4a4a;
}
*{margin:0;padding:0;box-sizing:border-box}
html,body{width:1003px;height:1200px;overflow:hidden;background:var(--bg)}
body{position:relative;font-family:"Barlow",sans-serif;color:var(--ink)}
.spread{position:absolute;left:38px;width:927px;height:232px;background:var(--paper);box-shadow:0 2px 6px rgba(0,0,0,.35)}
.spread::after{content:"";position:absolute;left:463px;top:0;bottom:0;width:1px;background:#d6d6d6}
.s1{top:58px}.s2{top:341px}.s3{top:623px}.s4{top:905px}
.abs{position:absolute}
.photo{position:absolute}
.warm{background:linear-gradient(135deg,#e6ddd2,var(--photo-warm))}
.cool{background:linear-gradient(135deg,#eef0f1,var(--photo-cool))}
.dark{background:linear-gradient(135deg,#777,var(--photo-dark))}
.mixed{background:linear-gradient(135deg,#f2f2f0,#b9a38a)}
.wordmark{position:absolute;display:flex;align-items:center;gap:4px;font-family:"Barlow",sans-serif;font-weight:600;color:var(--ink);letter-spacing:.5px}
.wordmark .sq{display:block;border:1.5px solid var(--green)}
.contact-box{position:absolute;left:13px;top:85px;width:437px;height:134px;background:var(--sand)}
.contact-row{position:absolute;left:18px;display:flex;gap:9px;font-family:"Barlow Semi Condensed",sans-serif;font-weight:600;font-size:6.4px;line-height:9.4px;color:var(--ink)}
.contact-row .icon{width:28px;height:28px;border:1.2px solid #fff;display:flex;align-items:center;justify-content:center;flex:none;margin-top:-2px}
.welcome{position:absolute;left:477px;top:88px;width:437px;height:131px;background:var(--green)}
.welcome p{position:absolute;left:13px;bottom:12px;font-weight:300;font-size:18.5px;color:#fff;white-space:nowrap}
.welcome b{font-weight:700}
.info-box{position:absolute;left:477px;top:13px;width:437px;height:205px;background:var(--sand-light)}
.info-box h2{position:absolute;left:17px;top:10px;font-weight:300;font-size:19px;color:#fff;letter-spacing:.2px}
.info-box .lead{position:absolute;left:17px;top:42px;font-family:"Barlow Semi Condensed",sans-serif;font-weight:600;font-size:6.6px;line-height:11.7px;color:var(--ink);white-space:nowrap}
.features{position:absolute;list-style:none;font-size:6.8px;line-height:11.7px;color:var(--ink-soft);white-space:nowrap}
.features li{position:relative;padding-left:8px}
.features li::before{content:"";position:absolute;left:0;top:3.5px;width:4px;height:4px;background:#fff}
.features .cont{padding-left:9px}
.features .cont::before{display:none}
.phone-title{position:absolute;left:477px;top:10px;font-weight:300;font-size:19.5px;color:var(--title-grey)}
.service{position:absolute;top:44px;width:140px}
.service h3{font-weight:700;font-size:8.8px;color:var(--green);letter-spacing:.2px}
.service .thumb{width:55px;height:55px;margin-top:4px}
.service p{margin-top:8px;font-size:6.8px;line-height:11.7px;color:var(--ink-soft);white-space:nowrap}
</style>
</head>
<body>

<!-- Rückseite & Titel -->
<section class="spread s1">
  <div class="wordmark" style="left:31px;top:49px;font-size:11px">
    <span class="sq" style="width:10px;height:10px"></span>KELVORA
  </div>
  <div class="photo cool" style="left:385px;top:13px;width:66px;height:65px" role="img" aria-label="Foto: Bürogebäude mit Straßenbahn"></div>
  <div class="contact-box">
    <div class="contact-row" style="top:20px">
      <span class="icon"><svg width="10" height="14" viewBox="0 0 10 14"><path d="M5 0a5 5 0 0 0-5 5c0 3.8 5 9 5 9s5-5.2 5-9a5 5 0 0 0-5-5zm0 7a2 2 0 1 1 0-4 2 2 0 0 1 0 4z" fill="#fff"/></svg></span>
      <span>KELVORA<br>Lindenstraße 14<br>40210 Musterstadt</span>
    </div>
    <div class="contact-row" style="top:58px">
      <span class="icon"><svg width="13" height="13" viewBox="0 0 24 24"><path d="M6.6 10.8a15 15 0 0 0 6.6 6.6l2.2-2.2c.3-.3.7-.4 1-.2 1.1.4 2.3.6 3.6.6.6 0 1 .4 1 1V20c0 .6-.4 1-1 1A17 17 0 0 1 3 4c0-.6.4-1 1-1h3.5c.6 0 1 .4 1 1 0 1.3.2 2.5.6 3.6.1.3 0 .7-.2 1z" fill="#fff"/></svg></span>
      <span>0800 5 000 123<br>Mo.-Fr. 08:00 - 20:00 Uhr</span>
    </div>
    <div class="contact-row" style="top:95px">
      <span class="icon"><svg width="14" height="10" viewBox="0 0 14 10"><rect width="14" height="10" fill="#fff"/><path d="M0 0l7 5.5L14 0" fill="none" stroke="#dcd5cf" stroke-width="1.2"/></svg></span>
      <span>info@kelvora.de<br>www.telefonservice-kelvora.de</span>
    </div>
  </div>

  <div class="photo cool" style="left:477px;top:13px;width:66px;height:65px" role="img" aria-label="Foto: Konferenzraum mit Fensterfront"></div>
  <div class="photo warm" style="left:551px;top:13px;width:66px;height:65px" role="img" aria-label="Foto: Empfangstresen aus Holz"></div>
  <div class="photo mixed" style="left:626px;top:13px;width:66px;height:65px" role="img" aria-label="Foto: entspannter Mann am Schreibtisch"></div>
  <div class="wordmark" style="left:703px;top:13px;height:65px;font-size:27px;gap:8px">
    <span class="sq" style="width:14px;height:14px"></span>KELVORA
  </div>
  <div class="welcome"><p>Willkommen in Ihrem neuen <b>KELVORA</b>!</p></div>
</section>

<!-- Büros auf Zeit -->
<section class="spread s2">
  <div class="photo cool" style="left:14px;top:13px;width:70px;height:205px" role="img" aria-label="Foto: heller Flur mit Einbauschränken"></div>
  <div class="photo mixed" style="left:91px;top:13px;width:212px;height:115px" role="img" aria-label="Foto: schwarzer Designersessel mit Beistelltisch"></div>
  <div class="photo mixed" style="left:91px;top:133px;width:109px;height:85px" role="img" aria-label="Foto: Laptop und Notizbuch auf Schreibtisch"></div>
  <div class="photo dark" style="left:206px;top:133px;width:97px;height:85px" role="img" aria-label="Foto: Kaffeemaschine mit Tasse"></div>
  <div class="photo warm" style="left:310px;top:13px;width:140px;height:205px" role="img" aria-label="Foto: Pendelleuchte und Pflanze auf Holztisch"></div>
  <div class="info-box">
    <h2>Büros auf Zeit</h2>
    <p class="lead">Sie sind auf der Suche nach exklusiven Büroräumen? Wir bieten Ihnen hochwertige und provisionsfreie<br>Räumlichkeiten auf Zeit – und das in bester Lage. Nach Vertragsunterzeichnung können Sie sofort einziehen: kein Umbau,<br>keine Renovierung und wenn Sie wünschen, können Sie das Mietverhältnis kurzfristig wieder<br>kündigen. Soviel Flexibiltät erhalten Sie nur bei uns!</p>
    <ul class="features" style="left:17px;top:114px">
      <li>Zugang 24/7</li>
      <li>persönlicher Empfang</li>
      <li>ab 15m²</li>
      <li>eigenes Firmenschild</li>
      <li>wöchentliche Reinigung inklusive</li>
      <li>kostenfreier Hochgeschwindigkeits-Internetzugang</li>
      <li>große Schreibtische</li>
    </ul>
    <ul class="features" style="left:232px;top:114px">
      <li>auf Wunsch inkl. Anrufannahme durch unser</li>
      <li class="cont">geschultes Personal</li>
      <li>optionale Anmietung eines Konferenzraumes</li>
      <li class="cont">mit bis zu 10 Plätzen</li>
      <li>Mitbenutzung der sanitären Einrichtungen</li>
      <li class="cont">und der Küche</li>
    </ul>
  </div>
</section>

<!-- Konferenzräume -->
<section class="spread s3">
  <div class="photo mixed" style="left:13px;top:13px;width:229px;height:115px" role="img" aria-label="Foto: Konferenztisch mit braunen Stühlen"></div>
  <div class="photo warm" style="left:247px;top:13px;width:203px;height:115px" role="img" aria-label="Foto: Konferenzstühle in Nahansicht"></div>
  <div class="photo warm" style="left:13px;top:133px;width:133px;height:85px" role="img" aria-label="Foto: Empfangsbereich mit Holztresen"></div>
  <div class="photo cool" style="left:152px;top:133px;width:53px;height:85px" role="img" aria-label="Foto: Stehleuchte"></div>
  <div class="photo cool" style="left:211px;top:133px;width:98px;height:85px" role="img" aria-label="Foto: Konferenztelefon"></div>
  <div class="photo mixed" style="left:315px;top:133px;width:135px;height:85px" role="img" aria-label="Foto: Konferenzraum mit Fernseher"></div>
  <div class="info-box">
    <h2>Konferenzräume</h2>
    <p class="lead">Nutzen Sie unsere modernen Konferenz- und Tagungsräume für Meetings, Präsentationen, Gespräche<br>oder Schulungen. Unsere hellen, stylischen Räume werden auch Sie faszinieren. Präsentieren Sie sich vor<br>Ihren Geschäftspartnern an einem tollen Ort. Unser Team erfüllt all Ihre Wünsche - vom leckeren Cappuccino<br>bis hin zu raffinierten Canapes.</p>
    <ul class="features" style="left:17px;top:136px">
      <li>bis zu 10 Teilnehmer</li>
      <li>bekannte Location im Lindenhaus</li>
      <li>persönlicher Empfang &amp; Betreuung</li>
      <li>55 Zoll 4k Fernseher</li>
      <li>MediaBox</li>
    </ul>
    <ul class="features" style="left:229px;top:136px">
      <li>Streamstick</li>
      <li>Konferenztelefon</li>
      <li>großes Whiteboard</li>
      <li>Flipchart</li>
      <li>Tiefgarage</li>
    </ul>
  </div>
</section>

<!-- Telefonservice -->
<section class="spread s4">
  <div class="photo mixed" style="left:13px;top:13px;width:437px;height:206px" role="img" aria-label="Foto: lächelnder Mann am Schreibtisch mit Computer"></div>
  <h2 class="phone-title">Unser Telefonservice</h2>
  <div class="service" style="left:477px">
    <h3>FlexCall</h3>
    <div class="thumb warm" role="img" aria-label="Foto: Mitarbeiterin mit Headset"></div>
    <p>Jeder verpasste Anruf kann eine verpasste<br>Chance sein. Deshalb gibt es FlexCall:<br>Egal ob Sie im Meeting, auf Außentermin<br>oder im Urlaub sind: Wir melden uns mit<br>Ihrem Firmennamen, nehmen Namen,<br>Rufnummer und Grund des Anrufs auf und<br>informieren Sie umgehend per Email oder<br>optional per SMS.</p>
  </div>
  <div class="service" style="left:627px">
    <h3>PraxisCall</h3>
    <div class="thumb cool" role="img" aria-label="Foto: Kalender mit Arzttermin"></div>
    <p>Terminvereinbarungen mit Ihren Patienten<br>über unseren Telefonservice? Sie werden<br>begeistert sein, wie einfach das ist! Mit<br>unseren Kooperationspartnern Terminara,<br>KalendoPlus, Medivo und Slotwerk füllt sich<br>Ihr Terminkalender wie von Zauberhand,<br>während Sie mit anderen wichtigen Dingen<br>beschäftigt sind.</p>
  </div>
  <div class="service" style="left:776px">
    <h3>FullCall</h3>
    <div class="thumb warm" role="img" aria-label="Foto: Bürogebäude"></div>
    <p>Bestell-, Ticket- oder Beschwerdehotline:<br>Mit FullCall haben Sie alles in einem<br>Tarif. Überzeugen Sie sich von unserer<br>langjährigen Erfahrung und vertrauen Sie<br>auf einen starken Partner an Ihrer Seite.</p>
  </div>
</section>

</body>
</html>
```